Executive Business Card for Healthcare Company [Need Today]

I need a business card design for a healthcare company. The only branding the company has thus far is a logo. The cards will be utilized by company executives. The design I envision will be vibrant and appealing but with a corporate feel. They shouldn't be too casual or playful. I would like to complete this project TODAY if possible.

Target Market(s)

Healthcare vendors, other executives in healthcare and pharmaceuticals

Industry/Entity Type

Pharmaceutical

Contact Information for Business Card

See attachment

Font styles to use
Serif
Sans Serif

Colors

Designer to choose colors to be used in the design.

```html
<!DOCTYPE html>
<html lang="en">
<head>
<meta charset="utf-8">
<title>Corvane Therapeutics – Business Card</title>
<link rel="stylesheet" href="https://fonts.googleapis.com/css2?family=Roboto:wght@300;400&display=swap">
<style>
  :root {
    --page-bg: #e6e3df;
    --card-bg: #f6f7f6;
    --card-edge: #d9dcda;
    --teal: #1f9aa6;
    --teal-name: #2a8f95;
    --text-grey: #4d5356;
    --brand-teal: #2a9d9c;
    --mark-fill: #d3ebe6;
  }
  html, body {
    margin: 0;
    padding: 0;
    width: 1200px;
    height: 1054px;
    overflow: hidden;
    background: var(--page-bg);
    font-family: "Roboto", Arial, sans-serif;
  }
  .canvas {
    position: relative;
    width: 1200px;
    height: 1054px;
  }
  .business-card {
    position: absolute;
    left: 100px;
    top: 224px;
    width: 1000px;
    height: 605px;
    background: var(--card-bg);
    border: 1px solid var(--card-edge);
    border-radius: 4px;
    box-shadow: 0 10px 30px rgba(0,0,0,0.12);
    overflow: hidden;
  }
  .brand-mark-area {
    position: absolute;
    left: -45px;
    top: 58px;
    width: 484px;
    height: 484px;
    border-radius: 50%;
    background: var(--mark-fill);
  }
  .brand-name {
    position: absolute;
    right: 88px;
    top: 56px;
    margin: 0;
    font-weight: 300;
    font-size: 50px;
    line-height: 1.12;
    color: var(--brand-teal);
    text-align: right;
    letter-spacing: 0.5px;
  }
  .contact-block {
    position: absolute;
    left: 521px;
    top: 262px;
    color: var(--text-grey);
  }
  .person-name {
    margin: 0;
    font-weight: 400;
    font-size: 40px;
    color: var(--teal-name);
    letter-spacing: 0.3px;
  }
  .person-title {
    margin: 6px 0 34px;
    font-weight: 300;
    font-size: 20px;
  }
  .contact-list {
    list-style: none;
    margin: 0;
    padding: 0;
    font-weight: 300;
    font-size: 25px;
  }
  .contact-list li {
    display: flex;
    align-items: center;
    gap: 12px;
    height: 36px;
  }
  .contact-icon {
    width: 22px;
    height: 22px;
    fill: var(--teal);
  }
  .address {
    margin: 12px 0 0;
    font-style: normal;
    font-weight: 300;
    font-size: 24px;
    line-height: 36px;
  }
</style>
</head>
<body>
<div class="canvas">
  <section class="business-card">
    <div class="brand-mark-area" role="img" aria-label="Company brand mark area"></div>

    <p class="brand-name">Corvane<br>Therapeutics</p>

    <div class="contact-block">
      <h1 class="person-name">Daniel Mercer</h1>
      <p class="person-title">Senior Director of Marketing</p>
      <ul class="contact-list">
        <li>
          <svg class="contact-icon" viewBox="0 0 24 24" aria-hidden="true">
            <path d="M3 9c0-3 4-5 9-5s9 2 9 5v1.5h-4.5V8.5c-1.2-.5-2.8-.8-4.5-.8s-3.3.3-4.5.8v2H3z"/>
            <path d="M6 12h12l2 8H4z"/>
          </svg>
          <span>555-214-0387</span>
        </li>
        <li>
          <svg class="contact-icon" viewBox="0 0 24 24" aria-hidden="true">
            <path d="M7 2h10a1.5 1.5 0 0 1 1.5 1.5v17A1.5 1.5 0 0 1 17 22H7a1.5 1.5 0 0 1-1.5-1.5v-17A1.5 1.5 0 0 1 7 2zm1 3v12h8V5zm4 13.5a1 1 0 1 0 0 2 1 1 0 0 0 0-2z"/>
          </svg>
          <span>555-608-1452</span>
        </li>
        <li>
          <svg class="contact-icon" viewBox="0 0 24 24" aria-hidden="true">
            <path d="M12 2a10 10 0 1 0 0 20 10 10 0 0 0 0-20zm6.9 9h-3a15 15 0 0 0-1.2-5.6A8 8 0 0 1 18.9 11zM12 4.1c.9 1.2 1.8 3.7 1.9 6.9h-3.8c.1-3.2 1-5.7 1.9-6.9zM9.3 5.4A15 15 0 0 0 8.1 11h-3a8 8 0 0 1 4.2-5.6zM5.1 13h3a15 15 0 0 0 1.2 5.6A8 8 0 0 1 5.1 13zm6.9 6.9c-.9-1.2-1.8-3.7-1.9-6.9h3.8c-.1 3.2-1 5.7-1.9 6.9zm2.7-1.3a15 15 0 0 0 1.2-5.6h3a8 8 0 0 1-4.2 5.6z"/>
          </svg>
          <span>dmercer@corvanerx.com</span>
        </li>
      </ul>
      <address class="address">118 N Lumpkin Avenue<br>Riverton, GA 30999</address>
    </div>
  </section>
</div>
</body>
</html>
```